Quorva - corporate Business Card

We need a good look and innovative business card for a new start up company based in Los Angeles called "Quorva". We are in a payment business, including payment card, app, and ewallet. We are expert in online payment and Card not present (CNP) transaction.
We need an innovative, modern business card.

Our logo font is Aero Matics

Target Market(s)

Startup - Bank - Online Payment - Card Manufacturing

Industry/Entity Type

Startup

Contact Information for Business Card

phone: 555 014 7396 - Address: 4172 Marlowe blvd, Calder Bay, CA 90299

Requirements
Must have
• Message: innovative, professional, expert, high tech, trust, online payment expert, security
Nice to have
• no comment
Should not have
• no Comment

```html
<!DOCTYPE html>
<html lang="en">
<head>
<meta charset="utf-8">
<title>Quorva – Business Card</title>
<link rel="stylesheet" href="https://fonts.googleapis.com/css2?family=Roboto:wght@400;500&display=swap">
<style>
  :root {
    --stage: #3b3430;
    --card: #151515;
    --card-edge: #202020;
    --brand-red: #d11f35;
    --silver: #b9b9b9;
    --silver-dim: #8a8a8a;
    --ink-light: #f2f2f2;
    --divider: #5a5a5a;
  }
  * { margin: 0; padding: 0; box-sizing: border-box; }
  html, body {
    width: 1200px; height: 864px; overflow: hidden;
    background: var(--stage);
    font-family: "Roboto", Arial, sans-serif;
  }
  .stage {
    width: 1200px; height: 864px;
    display: flex; flex-direction: column;
    align-items: center; justify-content: center; gap: 40px;
  }
  .card {
    width: 640px; height: 366px;
    background: var(--card);
    border: 1px solid var(--card-edge);
    border-radius: 4px;
    position: relative;
    box-shadow: 0 10px 30px rgba(0,0,0,.45);
  }

  /* Front */
  .card-front {
    display: flex; flex-direction: column;
    align-items: center; justify-content: center; gap: 30px;
  }
  .brand-name { font-weight: 500; line-height: 1; letter-spacing: 6px; text-transform: uppercase; }
  .card-front .brand-name { font-size: 58px; color: var(--silver-dim); }
  .front-web { font-size: 15px; letter-spacing: 7px; color: var(--silver); }

  /* Back */
  .card-back { display: flex; align-items: center; }
  .card-back .brand-area { width: 390px; display: flex; justify-content: center; }
  .card-back .brand-name { font-size: 44px; color: var(--brand-red); }
  .divider {
    width: 1px; height: 230px;
    background: linear-gradient(to bottom, transparent, var(--divider) 20%, var(--divider) 80%, transparent);
  }
  .contact { padding-left: 22px; color: var(--ink-light); font-size: 15px; line-height: 1.35; }
  .person-name { color: var(--brand-red); font-size: 20px; font-weight: 500; }
  .person-role { font-size: 18px; margin-bottom: 12px; }
  .address { margin-bottom: 10px; }
  .contact-line { display: flex; align-items: center; gap: 9px; margin-top: 3px; font-size: 15px; }
  .contact-line svg { width: 14px; height: 14px; fill: var(--brand-red); flex: none; }
</style>
</head>
<body>
<main class="stage">
  <section class="card card-front" aria-label="Card front">
    <span class="brand-name">Quorva</span>
    <p class="front-web">www.quorva.com</p>
  </section>

  <section class="card card-back" aria-label="Card back">
    <div class="brand-area">
      <span class="brand-name">Quorva</span>
    </div>
    <div class="divider"></div>
    <div class="contact">
      <p class="person-name">Marin Hale</p>
      <p class="person-role">President</p>
      <p class="address">4172 Marlowe blvd<br>Calder Bay, CA 90299</p>
      <p class="contact-line">
        <svg viewBox="0 0 16 16" aria-hidden="true"><path d="M3.6 1.2l2.3 2.6-1.3 1.9c.9 2 2.5 3.6 4.5 4.5l1.9-1.3 2.6 2.3-1.1 2.3C7 13.9 2.1 9 1.3 2.3z"/></svg>
        555 014 7396
      </p>
      <p class="contact-line">
        <svg viewBox="0 0 16 16" aria-hidden="true"><path d="M1 3h14v1.5L8 9 1 4.5z M1 6.3l7 4.5 7-4.5V13H1z"/></svg>
        marin@quorva.com
      </p>
      <p class="contact-line">
        <svg viewBox="0 0 16 16" aria-hidden="true"><path d="M8 1a7 7 0 1 0 0 14A7 7 0 0 0 8 1zm0 1.6c.8.9 1.4 2.3 1.6 4.6H6.4C6.6 4.9 7.2 3.5 8 2.6zM2.7 8.8h2.1c.1 1.8.5 3.2 1.1 4.3a5.5 5.5 0 0 1-3.2-4.3zm0-1.6a5.5 5.5 0 0 1 3.2-4.3c-.6 1.1-1 2.5-1.1 4.3zm3.7 1.6h3.2c-.2 2.3-.8 3.7-1.6 4.6-.8-.9-1.4-2.3-1.6-4.6zm4.8 0h2.1a5.5 5.5 0 0 1-3.2 4.3c.6-1.1 1-2.5 1.1-4.3zm0-1.6c-.1-1.8-.5-3.2-1.1-4.3a5.5 5.5 0 0 1 3.2 4.3z"/></svg>
        www.quorva.com
      </p>
    </div>
  </section>
</main>
</body>
</html>
```